Website for Reiki and Wellness Courses

I teach online courses in Reiki and wellness/self-development and am needing a new website.

The focus of the website will be to provide descriptions of the courses as well as include a blog and pages where students in my courses will visit for additional information.

Note: courses are NOT hosted on this site.
The focus of this website will be to encourage viewers to enroll in courses as well as opt in to the email list.

I will upload copy soon. My old website is: http://brightfernstudies.example. Please do not use existing logo.

Target Market(s)

Alternative health, wellness, spirituality, personal development. Males and females of all ages seeking to improve their health and life.

Industry/Entity Type

Health And Wellness

Logo Text

No text (please do not use existing logo)

Coding

Coded - Design and coding required

Number of Pages Required

5+ page

Requirements
Must have
• 1. Home page
• 2. About page
• 3. Courses page that outlines courses (there are currently 6 courses with 1 coming soon)
• 4. Individual course page (maybe a template that I can adjust color and pictures for with each course)
• 5. Blog
• 6. Student Area that outlines all Student Areas
• 7. Individual Student Area page (maybe a template that I can adjust color and pictures for with each course)
• 8. Shop page (note: items will not currently be purchased through website - it will be a link to quillmarket for a book).
• 9. Student thank-you page (maybe a template that I can adjust color and pictures for with each course) this is the page students are directed to at end of course with vouchers for other courses.
• Opt-in for the home page, course pages, blog and thank-you pages
Nice to have
• I would like the design to be calm, clean and soothing. Ideally visitors feel relaxed when viewing the site and are encouraged to explore the courses, subscribe to the email list and purchase a product.
• ~ Testimonials page
• ~ Contact page
• I tend to gravitate towards blues, greys and purples as well as monochromatic color schemes.
Should not have
• Contact form on home page
• phone number on home page
• location/physical address
• dates for blog posts

```html
<!DOCTYPE html>
<html lang="en">
<head>
<meta charset="utf-8">
<title>Bright Fern Studies – Reiki &amp; Wellness Courses</title>
<link rel="stylesheet" href="https://fonts.googleapis.com/css2?family=Montserrat:wght@400;600;700&family=Open+Sans:wght@400;600&display=swap">
<style>
  :root{
    --lavender:#6f6f93;
    --lavender-dark:#5b5b7d;
    --navy:#2c3344;
    --navy-deep:#262d3c;
    --paper:#ffffff;
    --mist:#f2f2f5;
    --ink:#2f3340;
    --muted:#8a8d99;
    --line:#dfe0e6;
    --hero-a:#d9d6d2;
    --hero-b:#9b9aa6;
    --meditate-a:#e9e7e4;
    --meditate-b:#c9c6c4;
  }
  *{box-sizing:border-box;margin:0;padding:0}
  html,body{width:813px;height:1200px;overflow:hidden}
  body{background:var(--paper);font-family:"Open Sans",Arial,sans-serif;color:var(--ink);position:relative}
  .heading{font-family:"Montserrat",Arial,sans-serif}

  /* header */
  .site-header{position:absolute;top:0;left:0;width:813px;height:60px;background:var(--paper);display:flex;align-items:center;padding:0 160px 0 168px;justify-content:space-between;box-shadow:0 1px 3px rgba(0,0,0,.06);z-index:3}
  .brand{display:flex;align-items:center;gap:7px;font-family:"Montserrat",Arial,sans-serif;font-size:11px;font-weight:600;color:var(--lavender-dark)}
  .brand-mark{width:14px;height:14px;background:var(--lavender)}
  .main-nav{display:flex;align-items:center;gap:14px}
  .main-nav a{font-family:"Montserrat",Arial,sans-serif;font-size:6.5px;font-weight:600;color:var(--ink);text-decoration:none;letter-spacing:.4px}
  .main-nav a.active{border-bottom:1px solid var(--ink);padding-bottom:2px}
  .search-btn{width:17px;height:17px;border-radius:50%;background:var(--lavender);display:flex;align-items:center;justify-content:center}

  /* hero */
  .hero{position:absolute;top:60px;left:0;width:813px;height:345px;background:linear-gradient(100deg,var(--hero-a) 0%,#cfcbc6 45%,var(--hero-b) 100%)}
  .hero-copy{position:absolute;top:55px;left:163px}
  .hero-kicker{font-size:6px;color:var(--muted);letter-spacing:.6px;margin-bottom:6px;border-bottom:1px solid var(--ink);display:inline-block;padding-bottom:2px}
  .hero-title{font-size:23px;font-weight:700;line-height:1.15;color:var(--ink)}

  .band{position:absolute;top:405px;left:0;width:813px;height:95px;background:var(--lavender)}
  .feature-cards{position:absolute;top:268px;left:168px;display:flex;gap:12px;z-index:2}
  .feature-card{width:151px;height:168px;background:var(--paper);box-shadow:0 2px 6px rgba(0,0,0,.12)}
  .feature-card .photo{height:88px}
  .feature-card .body{padding:9px 10px}
  .feature-card .tag{font-size:5px;color:var(--muted);margin-bottom:3px}
  .feature-card h3{font-size:7px;font-weight:700;line-height:1.25;margin-bottom:5px}
  .feature-card p{font-size:5px;line-height:1.5;color:var(--muted)}
  .btn{display:inline-block;font-family:"Montserrat",Arial,sans-serif;font-size:5.5px;font-weight:600;letter-spacing:.5px;padding:6px 14px;border-radius:2px;text-decoration:none}
  .btn-dark{background:var(--navy);color:var(--paper)}
  .btn-lavender{background:var(--lavender);color:var(--paper)}
  .band .btn{position:absolute;left:50%;top:60px;transform:translateX(-50%)}

  /* about */
  .about{position:absolute;top:500px;left:0;width:813px;height:186px;text-align:center}
  .section-title{font-size:16px;font-weight:600;color:var(--ink);margin-top:32px}
  .section-sub{font-size:5.5px;color:var(--muted);margin-top:3px}
  .about p{width:490px;margin:14px auto 0;font-size:5.5px;line-height:1.8;color:var(--muted);text-align:left}
  .about .actions{margin-top:14px;display:flex;gap:8px;justify-content:center}

  /* opt-in */
  .optin{position:absolute;top:688px;left:0;width:813px;height:232px;display:flex}
  .optin-panel{width:401px;background:var(--navy);padding:28px 0 0 168px;color:var(--paper)}
  .optin-panel .tag{font-size:5px;color:#9da3b4;margin-bottom:4px}
  .optin-panel h2{font-size:15px;font-weight:600;margin-bottom:6px}
  .optin-panel .intro{font-size:5.5px;line-height:1.6;color:#b8bdca;width:210px;margin-bottom:12px}
  .field{width:210px;height:17px;border:1px solid #4c5468;font-size:5.5px;color:#c7cbd6;padding:4px 7px;margin-bottom:6px}
  .optin-panel .btn{width:210px;text-align:center;background:#4a5266;margin-top:2px}
  .optin-photo{flex:1;background:linear-gradient(90deg,var(--meditate-a),var(--meditate-b))}

  /* testimonials */
  .testimonials{position:absolute;top:925px;left:0;width:813px;height:187px;background:var(--mist);text-align:center}
  .testimonials .section-title{margin-top:22px}
  .quotes{display:flex;gap:10px;justify-content:center;margin-top:16px}
  .quote{width:153px;height:50px;background:var(--paper);display:flex;align-items:center;gap:8px;padding:0 10px;text-align:left}
  .avatar{width:26px;height:26px;border-radius:50%;background:linear-gradient(135deg,#b8aea6,#7c7a88);flex:none}
  .quote h4{font-size:6.5px;font-weight:600;margin-bottom:2px}
  .quote p{font-size:5px;color:var(--muted);line-height:1.5}

  /* footer */
  .site-footer{position:absolute;top:1112px;left:0;width:813px;height:88px;background:var(--navy-deep);padding:25px 160px 0 160px;color:#9da3b4}
  .footer-links{display:flex;gap:14px}
  .footer-links a{font-size:5.5px;color:#c7cbd6;text-decoration:none}
  .copyright{font-size:5px;margin-top:6px}
  .social{position:absolute;right:160px;top:28px;display:flex;gap:6px}
  .social span{width:14px;height:14px;border-radius:50%;background:#4a5266;display:block}
  .to-top{position:absolute;right:160px;top:8px}
</style>
</head>
<body>

<header class="site-header">
  <div class="brand"><span class="brand-mark"></span>Bright Fern Studies</div>
  <nav class="main-nav">
    <a class="active" href="#">HOME</a>
    <a href="#">ABOUT</a>
    <a href="#">COURSES</a>
    <a href="#">BLOG</a>
    <a href="#">STUDENT AREA</a>
    <a href="#">CONTACT</a>
    <span class="search-btn">
      <svg width="8" height="8" viewBox="0 0 10 10"><circle cx="4" cy="4" r="3" fill="none" stroke="#fff" stroke-width="1.3"/><line x1="6.2" y1="6.2" x2="9" y2="9" stroke="#fff" stroke-width="1.3"/></svg>
    </span>
  </nav>
</header>

<section class="hero" role="img" aria-label="Photo of a reiki practitioner holding hands above a relaxed client lying down">
  <div class="hero-copy">
    <span class="hero-kicker">ONLINE COURSE</span>
    <h1 class="hero-title heading">BECOME A CERTIFIED<br>USUI REIKI MASTER</h1>
  </div>
</section>

<div class="feature-cards">
  <article class="feature-card">
    <div class="photo" role="img" aria-label="Photo of a reiki hand treatment on the head" style="background:linear-gradient(135deg,#d8cfc8,#9c8f8a)"></div>
    <div class="body">
      <div class="tag">Reiki Basics</div>
      <h3 class="heading">HOW REIKI WORKS</h3>
      <p>Discover how gentle energy healing brings calm and balance into daily life.</p>
    </div>
  </article>
  <article class="feature-card">
    <div class="photo" role="img" aria-label="Photo of stacked stones by calm water" style="background:linear-gradient(180deg,#c9d6de,#8ea4b2)"></div>
    <div class="body">
      <div class="tag">Certification</div>
      <h3 class="heading">TRADITIONAL USUI REIKI MASTER CERTIFICATION</h3>
      <p>Study every level at your own pace and earn your master certificate.</p>
    </div>
  </article>
  <article class="feature-card">
    <div class="photo" role="img" aria-label="Photo of a tranquil wellness setting" style="background:linear-gradient(135deg,#e3dcd6,#a79e9a)"></div>
    <div class="body">
      <div class="tag">Students</div>
      <h3 class="heading">RESOURCES</h3>
      <p>Guides, meditations and reading lists to support your practice each day.</p>
    </div>
  </article>
</div>

<section class="band">
  <a class="btn btn-dark" href="#">VIEW COURSES</a>
</section>

<section class="about">
  <h2 class="section-title heading">About Us</h2>
  <div class="section-sub">Learn, heal and grow with us</div>
  <p>Our online courses in reiki, wellness and self-development are created to help you feel calmer, healthier and more connected. Each course is taught step by step with clear lessons, guided practice and friendly support, so you can learn from home in your own time. Whether you are just beginning or ready to teach others, you will find a path that suits you and a community that cares about your growth.</p>
  <div class="actions">
    <a class="btn btn-dark" href="#">READ MORE</a>
    <a class="btn btn-lavender" href="#">COURSES</a>
  </div>
</section>

<section class="optin">
  <div class="optin-panel">
    <div class="tag">Newsletter</div>
    <h2 class="heading">Stay Inspired</h2>
    <p class="intro">Join our email list for gentle tips, new course news and special offers sent straight to your inbox.</p>
    <div class="field">First Name</div>
    <div class="field">Last Name</div>
    <div class="field">Email Address</div>
    <a class="btn" href="#">YES I WANT THIS!</a>
  </div>
  <div class="optin-photo" role="img" aria-label="Photo of a woman meditating in white clothing"></div>
</section>

<section class="testimonials">
  <h2 class="section-title heading">Testimonials</h2>
  <div class="section-sub">What our students say</div>
  <div class="quotes">
    <div class="quote"><span class="avatar" role="img" aria-label="Student portrait"></span><div><h4>John Doe</h4><p>Student, calm and clear course.</p></div></div>
    <div class="quote"><span class="avatar" role="img" aria-label="Student portrait"></span><div><h4>Miriam</h4><p>Student, truly life changing.</p></div></div>
    <div class="quote"><span class="avatar" role="img" aria-label="Student portrait"></span><div><h4>Selin Ovard</h4><p>Student, warm and helpful lessons.</p></div></div>
  </div>
</section>

<footer class="site-footer">
  <nav class="footer-links">
    <a href="#">Home</a><a href="#">Blog</a><a href="#">Privacy Policy</a><a href="#">Terms &amp; Conditions</a><a href="#">Contact</a>
  </nav>
  <div class="copyright">© Bright Fern Studies. All rights reserved.</div>
  <svg class="to-top" width="10" height="10" viewBox="0 0 10 10"><path d="M2 6 L5 3 L8 6" fill="none" stroke="#c7cbd6" stroke-width="1.2"/></svg>
  <div class="social"><span></span><span></span><span></span></div>
</footer>

</body>
</html>
```